New Email Marketing Design Project

I’d like you to make an email template. I’ll be welcoming and on boarding customers via email. And I’d like the branding to stand out. Keep it professional and simple. But be creative.

Design should look amazing on desktop and mobile phones.

Negative white space is ok.

Use stock images

I’ll like to have a spot for a picture of myself so make sure to include a circle where I can show my face so that email viewers will know who is speaking to them.

Target Market(s)

Practice managers, doctors, medical providers

Font styles to use
Sans Serif

Requirements
Must have
• Our Logo, CTA buttons, Same colors as website.
https://www.tarvoclaimservices.com

```html
<!DOCTYPE html>
<html lang="en">
<head>
<meta charset="utf-8">
<title>Tarvo Claim Services – Welcome</title>
<link rel="stylesheet" href="https://fonts.googleapis.com/css2?family=Bebas+Neue&family=Montserrat:ital,wght@0,300;0,400;0,700;1,700&family=Source+Sans+3:wght@400&display=swap">
<style>
  :root{
    --page-bg:#d9d9d9;
    --sky:#ddeef6;
    --navy:#0a3da6;
    --cyan:#0bb6e3;
    --teal-ring:#3a7fa0;
    --ink:#1b1b1b;
    --brand:#2f7aa1;
    --muted:#6a747c;
    --button:#9dd6dc;
    --footer:#a0a0a0;
    --white:#ffffff;
  }
  *{box-sizing:border-box;margin:0;padding:0}
  html,body{width:1200px;height:1200px;overflow:hidden;background:var(--page-bg)}
  .flyer{
    position:absolute;left:210px;top:16px;width:871px;height:1304px;
    transform:scale(0.8957);transform-origin:0 0;
    background:var(--sky);overflow:hidden;
    font-family:"Montserrat",sans-serif;
  }
  .flyer__art{position:absolute;inset:0;width:871px;height:1304px}
  .abs{position:absolute}
  .brand{left:60px;top:130px;display:flex;align-items:center;gap:12px}
  .brand__dot{width:34px;height:34px;border-radius:50%;background:var(--brand)}
  .brand__name{font-weight:700;font-size:19px;color:var(--brand);line-height:1.15;width:130px}
  .tagline{left:617px;top:64px;font-weight:700;font-style:italic;font-size:14px;color:var(--white)}
  .title{left:74px;top:290px;line-height:1}
  .title__bold{display:block;font-weight:700;font-size:48px;color:var(--ink)}
  .title__light{display:block;font-weight:400;font-size:62px;color:var(--brand);margin-top:6px;letter-spacing:0.5px}
  .intro{left:78px;top:414px;width:330px;font-size:14px;letter-spacing:1px;line-height:18px;color:var(--muted)}
  .services__heading{left:79px;top:582px;font-family:"Bebas Neue",sans-serif;font-size:40px;font-weight:400;color:var(--white);letter-spacing:0.5px}
  .services__label{top:710px;font-family:"Bebas Neue",sans-serif;font-size:21px;color:var(--white);white-space:nowrap}
  .body-copy{left:81px;top:791px;width:480px;font-family:"Source Sans 3",sans-serif;font-size:17px;line-height:20.3px;color:var(--white);white-space:nowrap}
  .cta{left:78px;top:943px;width:407px;height:58px;border-radius:29px;background:var(--button);
    display:flex;align-items:center;justify-content:center;gap:26px;
    font-family:"Bebas Neue",sans-serif;font-size:38px;color:var(--white);text-decoration:none;padding-top:4px}
  .cta__arrow{width:0;height:0;border-top:9px solid transparent;border-bottom:9px solid transparent;border-left:15px solid var(--white);margin-top:-6px}
  .news{left:75px;top:1016px;width:560px;color:var(--white);font-weight:700;font-size:13px}
  .news__title{font-size:13px;font-weight:700;margin-bottom:2px;line-height:16px}
  .news p{line-height:23.2px;white-space:nowrap}
  .footer{left:0;top:1204px;width:871px;height:100px;background:var(--footer);
    display:flex;align-items:center;padding:0 20px;gap:14px;color:var(--white);font-weight:700;font-size:9px}
  .footer__item{display:flex;align-items:center;gap:8px}
  .footer__social{margin-left:auto;display:flex;gap:10px}
  .footer__circle{width:36px;height:36px;border-radius:50%;border:2px solid #555}
</style>
</head>
<body>
<main class="flyer">
  <svg class="flyer__art" viewBox="0 0 871 1304">
    <defs>
      <linearGradient id="swoosh" x1="0" y1="0" x2="1" y2="1">
        <stop offset="0" stop-color="#0bc0e8"/><stop offset="1" stop-color="#0a4fb8"/>
      </linearGradient>
      <linearGradient id="band" x1="0" y1="0" x2="1" y2="0">
        <stop offset="0" stop-color="#0a3aa4"/><stop offset="0.55" stop-color="#0a78cf"/><stop offset="1" stop-color="#0bbce6" stop-opacity="0.9"/>
      </linearGradient>
      <linearGradient id="photoTone" x1="0" y1="0" x2="0" y2="1">
        <stop offset="0" stop-color="#dfe9ee"/><stop offset="1" stop-color="#f1f3f5"/>
      </linearGradient>
      <linearGradient id="portraitTone" x1="0" y1="0" x2="0" y2="1">
        <stop offset="0" stop-color="#d8dde2"/><stop offset="1" stop-color="#f2f4f6"/>
      </linearGradient>
    </defs>
    <path d="M369,0 L827,0 C760,90 640,230 560,265 C470,300 380,220 369,120 Z" fill="url(#swoosh)"/>
    <circle cx="515" cy="149" r="106" fill="url(#portraitTone)" stroke="var(--teal-ring)" stroke-width="6" role="img" aria-label="Portrait photo of the sender, a smiling doctor in a white coat"/>
    <rect x="560" y="300" width="311" height="904" fill="url(#photoTone)" role="img" aria-label="Stock photo of a smiling female doctor with a stethoscope holding a clipboard"/>
    <path d="M0,455 C180,510 420,620 560,780 C680,920 700,1080 630,1204 L0,1204 Z" fill="url(#band)"/>
    <line x1="84" y1="767" x2="459" y2="767" stroke="#ffffff" stroke-width="1.5"/>
    <g fill="none" stroke="#ffffff" stroke-width="2.5" stroke-linecap="round" stroke-linejoin="round">
      <circle cx="122" cy="669" r="27" fill="#0a7fd6" stroke="none"/>
      <path d="M122,684 L106,668 a8,8 0 0 1 16,-9 a8,8 0 0 1 16,9 Z"/>
      <path d="M103,669 h9 l4,-7 l5,12 l4,-5 h15"/>
      <circle cx="230" cy="669" r="27" fill="#0a7fd6" stroke="none"/>
      <rect x="214" y="660" width="32" height="22" rx="3"/>
      <path d="M224,660 v-4 h12 v4 M230,665 v12 M224,671 h12"/>
      <path d="M330,652 v12 a9,9 0 0 0 18,0 v-12 M339,673 c0,10 6,14 12,14 c5,0 8,-3 8,-8"/>
      <circle cx="359" cy="676" r="3"/>
      <circle cx="440" cy="669" r="27" fill="#0a7fd6" stroke="none"/>
      <path d="M429,652 h10 M431,652 v26 a3,3 0 0 0 6,0 v-26 M443,658 h10 M445,658 v20 a3,3 0 0 0 6,0 v-20"/>
    </g>
  </svg>

  <div class="abs brand"><span class="brand__dot"></span><span class="brand__name">Tarvo Claim Services</span></div>
  <p class="abs tagline">Lorem ipsum dolor</p>

  <h1 class="abs title"><span class="title__bold">Tarvo</span><span class="title__light">Claim Services</span></h1>
  <p class="abs intro">Lorem ipsum dolor sit amet, consecte-<br>tuer adipiscing elit, sed diam nonummy<br>nibh euismod tincidunt ut l</p>

  <h2 class="abs services__heading">Our Services</h2>
  <span class="abs services__label" style="left:79px">Lorem Ipsum</span>
  <span class="abs services__label" style="left:188px">Lorem Ipsum</span>
  <span class="abs services__label" style="left:300px">Lorem Ipsum</span>
  <span class="abs services__label" style="left:396px">Lorem Ipsum</span>

  <p class="abs body-copy">Lorem ipsum dolor sit amet, consectetuer adipiscing elit, sed<br>diam nonummy nibh euismod tincidunt ut laoreet dolore magna<br>aliquam erat volutpat. Ut wisi enim ad minim veniam, quis nos-<br>trud exerci tation ullamcorper suscipit lobortis nisl ut aliquip ex<br>ea commodo consequat. Duis autem vel eum iriure dolor in hen-<br>drerit in vulputate velit</p>

  <a class="abs cta" href="https://www.tarvoclaimservices.com">Find Out More <span class="cta__arrow"></span></a>

  <section class="abs news">
    <h3 class="news__title">REMOTE MEDICAL BILLING WORK ON THE RISE</h3>
    <p>Remote medical billing work on the rise thanks to COVID-19. Most people are not<br>ready to risk bringing contagion home to their families. Rightfully so, they are<br>choosing to not work at places where there are large crowds or many customers.<br>Preferring smaller less trafficked setting. The trend is only going to continue as<br>new platforms are made available every single week. It has been determined that<br>outsourcing is the way of the future for medical billing. Is your practice on</p>
  </section>

  <footer class="abs footer">
    <div class="footer__item">
      <svg width="22" height="30" viewBox="0 0 22 30"><path d="M11,29 C4,19 1,15 1,10 a10,10 0 0 1 20,0 c0,5 -3,9 -10,19 Z" fill="#fff"/><circle cx="11" cy="10" r="4" fill="var(--footer)"/></svg>
      <span>210 Harbor Ave Ste 400<br>Lakeview, Oregon 97630</span>
    </div>
    <div class="footer__item">
      <svg width="16" height="30" viewBox="0 0 16 30"><rect x="1" y="1" width="14" height="28" rx="2" fill="none" stroke="#fff" stroke-width="2"/><line x1="5" y1="25" x2="11" y2="25" stroke="#fff" stroke-width="2"/></svg>
      <span>555-014-0110</span>
    </div>
    <div class="footer__item">
      <svg width="26" height="24" viewBox="0 0 26 24"><rect x="1" y="8" width="24" height="15" rx="2" fill="#fff"/><rect x="6" y="1" width="14" height="9" fill="#fff"/></svg>
      <span>555-014-0110</span>
    </div>
    <div class="footer__item">
      <svg width="26" height="18" viewBox="0 0 26 18"><rect x="1" y="1" width="24" height="16" fill="none" stroke="#fff" stroke-width="2"/><path d="M1,1 L13,10 L25,1" fill="none" stroke="#fff" stroke-width="2"/></svg>
      <span>hello@tarvoclaimservices.com</span>
    </div>
    <div class="footer__social">
      <span class="footer__circle"></span><span class="footer__circle"></span><span class="footer__circle"></span><span class="footer__circle"></span>
    </div>
  </footer>
</main>
</body>
</html>
```